Marlowe Crest Realty business card design

Looking for an upscale and clean business card design and updated logo. I sell to a very high-end south Florida real estate market.
Target Market(s)
High-end real estate in south Florida real estate market
Industry/Entity Type
Real Estate Agent
Contact Information for Business Card
Marlowe Crest Realty, Inc
738 West Pinecrest Ave, Suite 410/510, Fort Lauderdale, FL 33308
Gary Whitlock - Broker/Owner
954-327-8846 Direct
garyshomes@quellmail.com
Website: DwellTarrowBay.com
Font styles to use
Other font styles liked:
- Copperplate Gothic, Georgia, etc.
Requirements
Must have
- My photo, company name, my name and title, all info stated in Details above
Nice to have
- Luxury home design element, waterfront

```html
<!DOCTYPE html>
<html lang="en">
<head>
<meta charset="utf-8">
<title>Marlowe Crest Realty – Business Card</title>
<link href="https://fonts.googleapis.com/css2?family=Sorts+Mill+Goudy&family=Open+Sans:wght@400;600&family=Michroma&display=swap" rel="stylesheet">
<style>
  :root{
    --backdrop:#7a4a28;
    --card:#ffffff;
    --ink:#111111;
    --black:#000000;
    --gold:#f4c73a;
    --muted:#333333;
  }
  *{margin:0;padding:0;box-sizing:border-box}
  html,body{width:1200px;height:816px;overflow:hidden}
  body{background:var(--backdrop);position:relative;font-family:"Open Sans",sans-serif;color:var(--ink)}
  .card{position:absolute;width:481px;height:274px;background:var(--card);border-radius:12px;overflow:hidden;box-shadow:0 3px 8px rgba(0,0,0,.45)}
  .card--front{left:96px;top:272px}
  .card--back{left:621px;top:271px}
  .wave{position:absolute;inset:0;width:100%;height:100%}
  .brand{position:absolute;display:flex;align-items:center;font-family:"Sorts Mill Goudy",serif;color:var(--ink);white-space:nowrap}
  .brand__dot{border-radius:50%;background:var(--gold);flex:none}
  .card--front .brand{left:22px;top:86px;font-size:10.5px;gap:8px}
  .card--front .brand__dot{width:30px;height:30px}
  .card--back .brand{left:82px;top:108px;font-size:21px;gap:14px}
  .card--back .brand__dot{width:60px;height:60px}
  .contacts{position:absolute;left:26px;top:163px;list-style:none}
  .contacts li{display:flex;align-items:center;height:20px;font-size:9.2px;margin-bottom:1px;white-space:nowrap}
  .contacts svg{width:14px;height:14px;margin-right:9px;flex:none}
  .person{position:absolute;right:33px;top:157px;text-align:right}
  .person__name{font-family:"Michroma",sans-serif;color:var(--gold);font-size:11.5px;letter-spacing:2.6px;margin-right:-2.6px;white-space:nowrap}
  .person__title{font-size:7.8px;color:var(--muted);margin-top:1px}
  .address{position:absolute;right:33px;top:214px;display:flex;align-items:flex-start;font-size:10.4px;line-height:15.5px;white-space:nowrap}
  .address svg{width:10px;height:15px;margin:6px 6px 0 0;flex:none}
</style>
</head>
<body>
  <section class="card card--front" aria-label="Business card front">
    <svg class="wave" viewBox="0 0 915 522" preserveAspectRatio="none" aria-hidden="true">
      <path fill="var(--black)" d="M0,0 H915 V140 C820,172 700,168 560,118 C420,68 330,22 240,20 C150,18 60,70 0,160 Z"/>
      <path fill="var(--gold)" d="M0,170 C60,78 150,26 240,26 C330,28 420,74 560,124 C700,174 820,178 915,146 V152 C820,196 700,192 560,150 C420,100 330,46 240,44 C150,44 60,92 0,172 Z"/>
    </svg>
    <div class="brand"><span class="brand__dot"></span>Marlowe Crest Realty, Inc</div>

    <ul class="contacts">
      <li><svg viewBox="0 0 24 24"><path fill="var(--gold)" d="M6.6 10.8a15 15 0 0 0 6.6 6.6l2.2-2.2c.3-.3.7-.4 1-.2 1.1.4 2.3.6 3.6.6.6 0 1 .4 1 1V20c0 .6-.4 1-1 1A17 17 0 0 1 3 4c0-.6.4-1 1-1h3.5c.6 0 1 .4 1 1 0 1.3.2 2.5.6 3.6.1.3 0 .7-.2 1z"/></svg>954-327-8846</li>
      <li><svg viewBox="0 0 24 24"><path fill="var(--gold)" d="M6 2h12v5H6zM3 8h18a1 1 0 0 1 1 1v7h-4v6H6v-6H2V9a1 1 0 0 1 1-1zm5 8v4h8v-4z"/></svg>954-327-8846</li>
      <li><svg viewBox="0 0 24 24"><path fill="var(--gold)" d="M2 5h20v14H2zm2 2v.5l8 5.5 8-5.5V7z"/></svg>garyshomes@quellmail.com</li>
      <li><svg viewBox="0 0 24 24"><g fill="none" stroke="var(--gold)" stroke-width="1.6"><circle cx="12" cy="12" r="9.5"/><ellipse cx="12" cy="12" rx="4.5" ry="9.5"/><path d="M2.5 12h19M4 7h16M4 17h16"/></g></svg>www.DwellTarrowBay.com</li>
    </ul>

    <div class="person">
      <p class="person__name">GARY WHITLOCK</p>
      <p class="person__title">Broker/Owner</p>
    </div>

    <div class="address">
      <svg viewBox="0 0 20 30"><path fill="var(--gold)" d="M10 0a10 10 0 0 1 10 10c0 7-10 20-10 20S0 17 0 10A10 10 0 0 1 10 0zm0 6a4 4 0 1 0 0 8 4 4 0 0 0 0-8z"/></svg>
      <p>738 West Pinecrest Ave, Suite 410/510<br>Fort Lauderdale, FL 33308</p>
    </div>
  </section>

  <section class="card card--back" aria-label="Business card back">
    <div class="brand"><span class="brand__dot"></span>Marlowe Crest Realty, Inc</div>
  </section>
</body>
</html>
```